Patent Law

Need to develop a home page for a patent lawyer.

Colors should go with logo, blues...

Company Name- Velun Tresk, PLLC

Company Overview-

I am an Intellectual Property Lawyer and focus on patents, copyrights, trademarks, & trade secrets. I work with small businesses and start ups in the chemical and biotech industries.

Why Us-

I am small firm that can provide large-firm service at a reasonable price. I also can charge flat-fees for entreprenuers in certain practice areas.

Services-
Intellectual Property
Patents
Copyrights
Trademarks
Trade secrets
Healthcare Compliance
Elder law
Wills
Trusts

Website we like-
http://www.quorvantlegal.example/ - within industry!!
http://www.daltrowemiko.example/
http://ulbrixtane.example/
http://thegravelcounsel.example/

Target Market(s)

My customers will be small business, specifically small start-up companies in the chemical and biotech arena.

Industry/Entity Type

Trade

Requirements
Must have
• Colors should go with logo, blues...

```html
<!DOCTYPE html>
<html lang="en">
<head>
<meta charset="utf-8">
<title>Velun Tresk, PLLC — Intellectual Property Law</title>
<link rel="stylesheet" href="https://fonts.googleapis.com/css2?family=Alegreya:ital,wght@1,700&family=Alegreya+Sans:ital,wght@0,400;0,500;0,700;1,400&display=swap">
<style>
:root{
  --blue:#0a87d8;
  --blue-dark:#0d4fa8;
  --navy:#1c2566;
  --ink:#1e2a4a;
  --text:#2b2b2b;
  --grey-panel:#f4f4f4;
  --grey-line:#c9c9c9;
  --white:#ffffff;
}
*{margin:0;padding:0;box-sizing:border-box}
html,body{width:1200px;height:1000px;overflow:hidden}
body{position:relative;background:var(--white);font-family:"Alegreya Sans",sans-serif;color:var(--text)}
.topbar{position:absolute;left:0;top:0;width:1200px;height:7px;background:var(--blue)}
.header{position:absolute;left:0;top:7px;width:1200px;height:108px;background:var(--white);box-shadow:0 3px 5px rgba(0,0,0,.25)}
.brand{position:absolute;left:158px;top:38px;display:flex;align-items:center;gap:10px;font-size:23px;font-weight:500;color:var(--ink);letter-spacing:.5px}
.brand-dot{width:22px;height:22px;border-radius:50%;background:var(--blue)}
.call{position:absolute;right:184px;top:28px;font-size:23px;font-weight:700;color:#4a4a4a}
.call span{color:var(--blue)}
.nav{position:absolute;left:513px;top:70px;width:514px;height:35px;border-top:2px dotted #7a7a7a;border-bottom:2px dotted #7a7a7a;background:linear-gradient(#fff 30%,#dbeefb 85%,#fff)}
.nav ul{list-style:none;display:flex;justify-content:flex-end;gap:22px;padding:8px 38px 0 0}
.nav li{font-size:13px;font-weight:500;color:var(--ink);letter-spacing:.2px}
.nav li.active{color:var(--blue-dark)}
.slider{position:absolute;left:176px;top:134px;width:849px;height:358px;border-radius:10px;background:linear-gradient(#f7f7f7,#dcdcdc);border:1px solid #c4c4c4;box-shadow:0 12px 14px -8px rgba(0,0,0,.35)}
.slide-photo{position:absolute;left:13px;top:13px;width:823px;height:327px;border-radius:8px;background:linear-gradient(100deg,#e9ebee 0%,#c8cdd4 30%,#a7b1bd 55%,#d9d6d0 75%,#6c7176 100%)}
.arrow{position:absolute;top:279px;width:40px;height:40px;border-radius:50%;background:radial-gradient(circle at 40% 35%,#fff,#cfcfcf);border:1px solid #b5b5b5;box-shadow:0 0 0 6px #eee,0 0 0 7px #cfcfcf}
.arrow.prev{left:158px}.arrow.next{left:1005px}
.arrow svg{position:absolute;left:9px;top:11px}
.quote{position:absolute;left:688px;top:147px;width:228px;height:296px;background:rgba(245,245,245,.82);border-bottom:6px solid var(--blue);text-align:center}
.quote .rule{position:absolute;left:30px;width:168px;height:5px;border-top:1px solid #777;border-bottom:1px solid #777}
.quote p{position:absolute;left:14px;top:44px;width:200px;font-family:"Alegreya",serif;font-style:italic;font-weight:700;font-size:16.5px;line-height:22.5px;color:#3a3a3a}
.quote .mini{position:absolute;left:0;top:242px;width:100%;font-size:9px;color:var(--ink)}
.features{position:absolute;left:175px;top:517px;width:847px;height:316px;background:var(--grey-panel);border-radius:5px;box-shadow:0 8px 10px -8px rgba(0,0,0,.3)}
.col-sep{position:absolute;top:0;width:2px;height:255px;background:linear-gradient(#ccc,#e6e6e6)}
.ribbon{position:absolute;top:14px;width:151px;height:61px}
.ribbon span{position:absolute;left:58px;top:14px;color:#fff;font-weight:700;font-size:14.5px;letter-spacing:.2px}
.ribbon svg.icon{position:absolute;left:14px;top:6px}
.col-text{position:absolute;top:98px;font-style:italic;font-size:12px;line-height:20.5px;color:var(--text)}
.services{position:absolute;list-style:none;font-style:italic;font-size:12px;line-height:13px}
.services li{position:absolute;padding-left:17px;width:100px}
.services li::before{content:"";position:absolute;left:0;top:2px;border-left:8px solid #111;border-top:4px solid transparent;border-bottom:4px solid transparent}
.footer{position:absolute;left:0;top:860px;width:1200px;height:140px;background:linear-gradient(#0a7fd2,#1c2a6e)}
.world{position:absolute;left:169px;top:21px;width:217px;height:100px;border-radius:40px;background:radial-gradient(ellipse at 50% 50%,#d6d6d6 0%,#b8bcc4 60%,rgba(184,188,196,0) 72%)}
.foot-nav{position:absolute;left:452px;top:94px;display:flex;gap:19px;list-style:none;font-size:9.5px;color:#fff}
.copyright{position:absolute;left:452px;top:111px;width:326px;text-align:center;font-size:9px;color:#fff}
.foot-brand{position:absolute;left:862px;top:56px;display:flex;align-items:center;gap:8px;font-size:19px;font-weight:500;color:#fff}
.foot-brand .brand-dot{width:18px;height:18px;background:#fff}
</style>
</head>
<body>
<div class="topbar"></div>
<header class="header">
  <div class="brand"><span class="brand-dot"></span>Velun Tresk, PLLC</div>
  <div class="call">CALL US : <span>333-555-918</span></div>
  <nav class="nav"><ul>
    <li class="active">HOME</li><li>ABOUT</li><li>PRACTICES</li><li>PEOPLE</li><li>BLOGS</li><li>NEWS</li><li>CONTACT</li>
  </ul></nav>
</header>

<section class="slider">
  <div class="slide-photo" role="img" aria-label="Photo of a lawyer advising two clients at a desk"></div>
</section>
<div class="arrow prev"><svg width="22" height="18" viewBox="0 0 22 18"><path d="M9 2 2 9l7 7M2 9h18" fill="none" stroke="#7a7a7a" stroke-width="3"/></svg></div>
<div class="arrow next"><svg width="22" height="18" viewBox="0 0 22 18"><path d="M13 2l7 7-7 7M20 9H2" fill="none" stroke="#7a7a7a" stroke-width="3"/></svg></div>
<div class="quote">
  <div class="rule" style="top:26px"></div>
  <p>I am an Intellectual Property Lawyer and focus on patents, copyrights, trademarks, &amp; trade secrets. I work with small businesses and start ups in the chemical and biotech industries.</p>
  <div class="mini">Velun Tresk, PLLC</div>
  <div class="rule" style="top:265px"></div>
</div>

<section class="features">
  <div class="col-sep" style="left:282px"></div>
  <div class="col-sep" style="left:566px"></div>

  <div class="ribbon" style="left:69px">
    <svg width="151" height="61"><defs><linearGradient id="rb" x1="0" y1="0" x2="0" y2="1"><stop offset="0" stop-color="#1a66c4"/><stop offset="1" stop-color="#0a92e0"/></linearGradient></defs><polygon points="0,0 151,0 151,61 75.5,46 0,61" fill="url(#rb)"/></svg>
    <svg class="icon" width="32" height="32" viewBox="0 0 32 32"><path d="M3 6v20l5-5 4 8 3-1-4-8h7z" fill="#fff"/><path d="M20 6a5 5 0 1 1 6 5v3M26 18v2" fill="none" stroke="#fff" stroke-width="2.5"/></svg>
    <span>WHY US</span>
  </div>
  <div class="ribbon" style="left:373px">
    <svg width="151" height="61"><polygon points="0,0 151,0 151,61 75.5,46 0,61" fill="url(#rb)"/></svg>
    <svg class="icon" width="32" height="32" viewBox="0 0 32 32" fill="none" stroke="#fff" stroke-width="2"><circle cx="5" cy="7" r="3"/><circle cx="5" cy="16" r="3"/><circle cx="5" cy="25" r="3"/><path d="M12 6h16M12 10h12M12 15h16M12 19h12M12 24h16"/></svg>
    <span>WHAT WE DO</span>
  </div>
  <div class="ribbon" style="left:657px">
    <svg width="151" height="61"><polygon points="0,0 151,0 151,61 75.5,46 0,61" fill="url(#rb)"/></svg>
    <span>CONTACT</span>
  </div>

  <p class="col-text" style="left:44px;width:226px">I am small firm that can provide large-firm service at a reasonable price. I also can charge flat-fees for entreprenuers in certain practice areas.</p>

  <ul class="services" style="left:334px;top:105px">
    <li style="top:0">Intellectual Property</li>
    <li style="top:36px">Copyrights</li>
    <li style="top:59px">Trade secrets</li>
    <li style="top:81px">Elder law</li>
    <li style="top:104px">Trusts</li>
  </ul>
  <ul class="services" style="left:460px;top:105px">
    <li style="top:0">Patents</li>
    <li style="top:23px">Trademarks</li>
    <li style="top:46px">Healthcare Compliance</li>
    <li style="top:90px">Wills</li>
  </ul>

  <p class="col-text" style="left:608px;width:230px">I am an Intellectual Property Lawyer and focus on patents, copyrights, trademarks, &amp; trade secrets. I work with small businesses and start ups in the chemical and biotech industries.<br>I am small firm that can provide large-firm service at a reasonable price. I also can charge flat-fees for entrepreneurs in certain practice areas.</p>
</section>

<footer class="footer">
  <div class="world" role="img" aria-label="World map illustration"></div>
  <ul class="foot-nav"><li>HOME</li><li>ABOUT</li><li>PRACTICES</li><li>PEOPLE</li><li>BLOGS</li><li>NEWS</li><li>CONTACT</li></ul>
  <p class="copyright">copyright@Velun Tresk, PLLC all reserved.</p>
  <div class="foot-brand"><span class="brand-dot"></span>Velun Tresk, PLLC</div>
</footer>
</body>
</html>
```